All Natural Mosquito Repellent

My company, BrightPebble Company has created an all natural mosquito repellent. I already have other all natural products that I have developed and created labels for. I will include a copy of that label so you have something to work from. I will need two labels. One for the front of the bottle and one for the back. The back label will need space for a UPC. The labels need to be 63mm (H) x 39mm (W)

Target Market(s)

Consumers, Organic, People who like natural products

Font styles to use
Other font styles liked:
• A combination of both Serif and Sans Serif

Requirements
Must have
• Use the words Organic, All Natural, Travel size, made in the USA label
Nice to have
• tag line: Don't beat them off. Spray them away.

```html
<!DOCTYPE html>
<html lang="en">
<head>
<meta charset="utf-8">
<title>BrightPebble Company — All Natural Mosquito Repellent Labels</title>
<link href="https://fonts.googleapis.com/css2?family=Bangers&family=Roboto+Slab:wght@700&display=swap" rel="stylesheet">
<style>
  :root {
    --page: #d9d9db;
    --paper: #ffffff;
    --forest: #1e4a2b;
    --forest-deep: #0f2a18;
    --leaf: #3f8a3a;
    --leaf-dark: #2d6a2c;
    --ink: #1b1b1b;
    --cream: #f2f2f2;
    --alert: #d8242a;
  }
  * { box-sizing: border-box; margin: 0; padding: 0; }
  html, body { width: 840px; height: 1200px; overflow: hidden; }
  body { background: var(--page); position: relative; font-family: "Bangers", sans-serif; }

  .label {
    position: absolute; left: 60px; width: 720px; height: 424px;
    box-shadow: 0 10px 24px rgba(0,0,0,.35);
    overflow: hidden;
  }
  .label--front { top: 130px; }
  .label--back { top: 646px; }
  .label-bg { position: absolute; inset: 0; }

  .brand {
    position: absolute; top: 42px; left: 0; right: 0;
    display: flex; align-items: center; justify-content: center; gap: 10px;
    font-family: "Roboto Slab", serif; font-weight: 700; font-size: 34px;
    color: var(--ink); letter-spacing: .5px; line-height: 1;
  }
  .brand-dot { width: 36px; height: 36px; border-radius: 50%; background: var(--ink); }

  .abs { position: absolute; line-height: 1; }
  .txt-light { color: var(--cream); }

  /* front */
  .front-kicker { left: 262px; top: 120px; font-size: 30px; letter-spacing: 1px; }
  .front-title { left: 104px; top: 150px; font-size: 100px; letter-spacing: 2px; }
  .front-sub { left: 340px; top: 246px; font-size: 46px; letter-spacing: 1px; }
  .travel { left: 66px; top: 264px; width: 72px; height: 72px; border-radius: 50%; background: #143d22; border: 2px solid var(--leaf);
    display: flex; align-items: center; justify-content: center; text-align: center; font-size: 13px; line-height: 1.05; }
  .usa { left: 50px; top: 358px; display: flex; align-items: center; gap: 8px; font-size: 24px; line-height: .95; }
  .usa-dot { width: 38px; height: 38px; border-radius: 50%; background: var(--cream); }
  .net { left: 386px; top: 352px; text-align: center; width: 110px; }
  .net-label { font-size: 16px; display: block; }
  .net-value { font-size: 34px; display: block; }
  .organic { font-family: "Roboto Slab", serif; font-weight: 700; color: var(--cream); text-align: center; }
  .organic--front { left: 529px; top: 330px; width: 152px; font-size: 30px; }
  .organic--back { left: 129px; top: 148px; width: 90px; font-size: 16px; }

  /* back */
  .back-head { left: 0; width: 720px; top: 118px; text-align: center; }
  .back-kicker { font-size: 15px; display: block; }
  .back-title { font-size: 48px; display: block; letter-spacing: 1px; }
  .back-sub { font-size: 22px; display: block; }
  .copy { font-size: 11.5px; line-height: 17px; letter-spacing: .4px; color: var(--cream); }
  .copy--one { left: 72px; width: 576px; top: 214px; text-align: center; }
  .copy--two { left: 72px; width: 576px; top: 290px; text-align: center; }
  .copy--three { left: 72px; width: 270px; top: 350px; text-align: center; }
  .upc-space { left: 488px; top: 334px; width: 180px; height: 72px; background: var(--paper); }
</style>
</head>
<body>

  <section class="label label--front" aria-label="Front label">
    <svg class="label-bg" width="720" height="424" viewBox="0 0 720 424">
      <defs>
        <radialGradient id="forestFront" cx="50%" cy="45%" r="70%">
          <stop offset="0" stop-color="#255a33"/>
          <stop offset="1" stop-color="#0f2a18"/>
        </radialGradient>
      </defs>
      <rect width="720" height="424" fill="#ffffff"/>
      <path d="M0 128 Q360 100 720 128 V424 H0 Z" fill="url(#forestFront)"/>
      <circle cx="267" cy="318" r="56" fill="#1b1b1b" role="img" aria-label="Cartoon mosquito inside a red no-entry sign"/>
      <circle cx="267" cy="318" r="51" fill="none" stroke="#d8242a" stroke-width="10"/>
      <ellipse cx="605" cy="345" rx="76" ry="56" fill="#3f8a3a" role="img" aria-label="Green leaf organic badge"/>
    </svg>

    <div class="brand"><span class="brand-dot"></span>BRIGHTPEBBLE CO.</div>

    <div class="abs front-kicker txt-light">ALL NATURAL</div>
    <div class="abs front-title txt-light">MOSQUITO</div>
    <div class="abs front-sub txt-light">REPELLENT</div>

    <div class="abs travel txt-light">TRAVEL<br>SIZE</div>
    <div class="abs usa txt-light"><span class="usa-dot"></span><span>MADE IN<br>USA</span></div>
    <div class="abs net txt-light"><span class="net-label">NET WEIGHT</span><span class="net-value">125 ML</span></div>
    <div class="abs organic organic--front">Organic</div>
  </section>

  <section class="label label--back" aria-label="Back label">
    <svg class="label-bg" width="720" height="424" viewBox="0 0 720 424">
      <defs>
        <radialGradient id="forestBack" cx="50%" cy="45%" r="70%">
          <stop offset="0" stop-color="#255a33"/>
          <stop offset="1" stop-color="#0f2a18"/>
        </radialGradient>
      </defs>
      <rect width="720" height="424" fill="#ffffff"/>
      <path d="M0 128 Q360 100 720 128 V424 H0 Z" fill="url(#forestBack)"/>
      <ellipse cx="174" cy="157" rx="46" ry="28" fill="#3f8a3a" role="img" aria-label="Small green leaf organic badge"/>
      <circle cx="517" cy="152" r="30" fill="#1b1b1b" role="img" aria-label="Small mosquito inside a red no-entry sign"/>
      <circle cx="517" cy="152" r="27" fill="none" stroke="#d8242a" stroke-width="6"/>
    </svg>

    <div class="brand"><span class="brand-dot"></span>BRIGHTPEBBLE CO.</div>

    <div class="abs back-head txt-light">
      <span class="back-kicker">ALL NATURAL</span>
      <span class="back-title">MOSQUITO</span>
      <span class="back-sub">REPELLENT</span>
    </div>
    <div class="abs organic organic--back">Organic</div>

    <p class="abs copy copy--one">A GENTLE BLEND OF PLANT OILS THAT KEEPS BITING INSECTS AWAY FROM SKIN AND CLOTHING. SHAKE WELL BEFORE EACH USE AND SPRAY EVENLY OVER EXPOSED AREAS. REAPPLY EVERY TWO HOURS OR AFTER SWIMMING. SAFE FOR THE WHOLE FAMILY OUTDOORS.</p>
    <p class="abs copy copy--two">INGREDIENTS: WITCH HAZEL, CITRONELLA OIL, LEMONGRASS OIL, PEPPERMINT OIL, CEDARWOOD OIL, ROSEMARY OIL AND PURIFIED WATER. AVOID CONTACT WITH EYES. KEEP OUT OF REACH OF CHILDREN.</p>
    <p class="abs copy copy--three">STORE IN A COOL, DRY PLACE. DO NOT USE ON BROKEN SKIN. MADE IN SMALL BATCHES.</p>

    <div class="abs upc-space" aria-label="Space reserved for UPC"></div>
  </section>

</body>
</html>
```